Flyer Design Project

Training and Consulting Flyer
Updates

I attached a document that contained the wording for the flyer as well as the logo.

Target Market(s)

Maple Bridge agencies and grantees

Industry/Entity Type

Training

Font styles to use
Sans Serif

Colors
e667a6
eda3c7
a54499
b768aa
f9d9e8

Requirements
Must have
• Words provided on attachment
Nice to have
• Graphics that are related to adult training/learning and consulting

```html
<!DOCTYPE html>
<html lang="en">
<head>
<meta charset="utf-8">
<title>Lumen Health Consultants – Training and Consulting Flyer</title>
<link href="https://fonts.googleapis.com/css2?family=Quicksand:wght@500;600;700&family=Open+Sans:wght@400;600&display=swap" rel="stylesheet">
<style>
  :root {
    --pink: #c2307a;
    --pink-deep: #a8246a;
    --pink-soft: #e667a6;
    --pink-pale: #f9d9e8;
    --grey-dark: #5f5f5f;
    --grey-mid: #8a8a8a;
    --grey-light: #cfcfcf;
    --ink: #222222;
    --paper: #ffffff;
    --stage: #ececec;
  }
  * { margin: 0; padding: 0; box-sizing: border-box; }
  html, body { width: 1200px; height: 1200px; overflow: hidden; background: var(--stage); }
  .flyer {
    position: absolute; left: 152px; top: 20px;
    width: 896px; height: 1160px;
    background: var(--paper);
    overflow: hidden;
    font-family: "Open Sans", Arial, sans-serif;
    box-shadow: 0 4px 18px rgba(0,0,0,.15);
  }
  .flyer-shapes { position: absolute; inset: 0; }
  .team-photo { position: absolute; left: 371px; top: 23px; width: 525px; height: 390px; }

  .brand { position: absolute; left: 150px; top: 66px; display: flex; align-items: center; gap: 12px; }
  .brand-dot { width: 34px; height: 34px; border-radius: 50%; background: var(--pink); }
  .brand-name {
    font-family: "Quicksand", Arial, sans-serif; font-weight: 700;
    font-size: 25px; line-height: 27px; color: var(--ink); text-transform: uppercase;
  }
  .tagline { position: absolute; left: 178px; top: 160px; font-size: 14px; color: var(--ink); letter-spacing: .3px; }

  .pillars { position: absolute; left: 112px; top: 212px; list-style: none; }
  .pillars li {
    height: 57px; line-height: 57px;
    font-family: "Quicksand", Arial, sans-serif; font-weight: 700; font-size: 38px;
  }
  .pillars li:nth-child(2) { margin-left: 7px; }
  .pillars li:nth-child(3) { margin-left: 13px; }
  .pillars .word-pink { color: var(--pink); }
  .pillars .word-grey { color: var(--grey-dark); }

  .section-title {
    position: absolute; left: 245px; width: 600px; top: 458px; text-align: center;
    font-family: "Quicksand", Arial, sans-serif; font-weight: 700; font-size: 35px; color: var(--pink);
  }
  .services { position: absolute; left: 215px; top: 520px; width: 630px; list-style: none; }
  .services li {
    position: relative; padding-left: 30px; margin-bottom: 19.5px;
    font-size: 14.4px; line-height: 19.3px; color: var(--ink); text-align: justify;
  }
  .services li svg { position: absolute; left: 0; top: 1px; width: 19px; height: 19px; }

  .ceo-photo { position: absolute; left: 82px; top: 951px; width: 156px; height: 156px; border-radius: 50%; }
  .ceo-name {
    position: absolute; left: 269px; top: 982px;
    font-family: "Quicksand", Arial, sans-serif; font-weight: 700; font-size: 27px; color: var(--pink);
  }
  .ceo-phone {
    position: absolute; left: 269px; top: 1022px; display: flex; align-items: center; gap: 7px;
    font-family: "Quicksand", Arial, sans-serif; font-weight: 700; font-size: 18px; color: var(--grey-dark);
  }
  .footer-contact {
    position: absolute; top: 1107px; left: 264px; right: 50px;
    display: flex; justify-content: space-between; color: #fff; font-size: 15.5px;
  }
  .footer-contact span { display: flex; align-items: center; gap: 8px; }
</style>
</head>
<body>
<article class="flyer">
  <svg class="flyer-shapes" width="896" height="1160" viewBox="0 0 896 1160">
    <defs>
      <linearGradient id="sidePanel" x1="0" y1="0" x2="1" y2="0">
        <stop offset="0" stop-color="#6e6e6e"/>
        <stop offset="0.6" stop-color="#9a9a9a"/>
        <stop offset="1" stop-color="#c8c8c8"/>
      </linearGradient>
      <linearGradient id="footerBand" x1="0" y1="0" x2="1" y2="0">
        <stop offset="0" stop-color="#b52a72"/>
        <stop offset="1" stop-color="#e667a6"/>
      </linearGradient>
    </defs>
    <path d="M0 0 H110 C140 150 165 330 155 450 L155 1060 L0 1080 Z" fill="url(#sidePanel)"/>
    <path d="M55 0 H95 C120 200 140 380 130 520 L130 1080 L90 1085 L95 500 C100 360 85 180 55 0 Z" fill="#ffffff" opacity=".18"/>
    <path d="M164 555 C166 520 163 470 158 418" stroke="var(--pink)" stroke-width="5" fill="none"/>
    <path d="M164 430 L164 1000" stroke="var(--pink)" stroke-width="5"/>
    <path d="M164 444 C380 410 620 410 896 440 L896 453 C620 424 380 424 164 460 Z" fill="var(--pink)"/>
  </svg>

  <div class="team-photo" role="img" aria-label="Photo of a smiling team of four business professionals with arms crossed"
       style="background:linear-gradient(90deg,#ffffff 0%,#e3ebf5 30%,#b9cde8 70%,#7ea3d8 100%);clip-path:path('M0 0 H525 V395 C400 382 260 378 0 405 Z');opacity:.85"></div>

  <div class="brand"><span class="brand-dot"></span><span class="brand-name">Lumen<br>Health<br>Consultants</span></div>
  <p class="tagline">TOGETHER WE CAN</p>

  <ul class="pillars">
    <li class="word-pink">Learning</li>
    <li class="word-grey">Guidance</li>
    <li class="word-pink">Results</li>
  </ul>

  <h1 class="section-title">Health Consultants &amp; Group</h1>

  <ul class="services">
    <li><svg viewBox="0 0 20 20"><circle cx="10" cy="10" r="8.5" fill="none" stroke="var(--pink)" stroke-width="2"/><path d="M6 10.3l2.8 2.8L14.3 7.4" fill="none" stroke="var(--pink)" stroke-width="2"/></svg>Innovative Approaches to meeting the 5 year funding measures in the content area of health, Nutrition, Oral Health &amp; Safety.</li>
    <li><svg viewBox="0 0 20 20"><circle cx="10" cy="10" r="8.5" fill="none" stroke="var(--pink)" stroke-width="2"/><path d="M6 10.3l2.8 2.8L14.3 7.4" fill="none" stroke="var(--pink)" stroke-width="2"/></svg>Lumen Health Consultants has embarked on a New methodology designed to ensure Programs meet total requirements as Prescribed under the Health Service Program.</li>
    <li><svg viewBox="0 0 20 20"><circle cx="10" cy="10" r="8.5" fill="none" stroke="var(--pink)" stroke-width="2"/><path d="M6 10.3l2.8 2.8L14.3 7.4" fill="none" stroke="var(--pink)" stroke-width="2"/></svg>Let us manage your health Program through remote and offsite measures to ensure total compliance and strategic methodology toward quality service approaches.</li>
    <li><svg viewBox="0 0 20 20"><circle cx="10" cy="10" r="8.5" fill="none" stroke="var(--pink)" stroke-width="2"/><path d="M6 10.3l2.8 2.8L14.3 7.4" fill="none" stroke="var(--pink)" stroke-width="2"/></svg>Let us provide consultants to mentor your health manager nutrition content specialist facilities safety manager. These support consultant are advanced level academias in their specialised areas of focus.</li>
    <li><svg viewBox="0 0 20 20"><circle cx="10" cy="10" r="8.5" fill="none" stroke="var(--pink)" stroke-width="2"/><path d="M6 10.3l2.8 2.8L14.3 7.4" fill="none" stroke="var(--pink)" stroke-width="2"/></svg>Let us provide consultants to mentor your health manager nutrition content specialist facilities safety manager. These support consultant are advanced level academias in their specialised areas of focus.</li>
    <li><svg viewBox="0 0 20 20"><circle cx="10" cy="10" r="8.5" fill="none" stroke="var(--pink)" stroke-width="2"/><path d="M6 10.3l2.8 2.8L14.3 7.4" fill="none" stroke="var(--pink)" stroke-width="2"/></svg>Let us provide advanced Based Mock Reviews for your program designed to assist management staff in focus (i), Focus (ii), Review Strategies for 2018.</li>
    <li><svg viewBox="0 0 20 20"><circle cx="10" cy="10" r="8.5" fill="none" stroke="var(--pink)" stroke-width="2"/><path d="M6 10.3l2.8 2.8L14.3 7.4" fill="none" stroke="var(--pink)" stroke-width="2"/></svg>Let us provide T/TA for any New health, nutrition, Safety staff to ensure they are fully prepared to perform their job duties at their highest level of management approaches.</li>
  </ul>

  <svg class="flyer-shapes" width="896" height="1160" viewBox="0 0 896 1160">
    <path d="M0 1120 C260 1070 560 1070 896 1105 L896 1160 L0 1160 Z" fill="url(#footerBand)"/>
    <path d="M200 1072 C480 1062 700 1072 896 1098" stroke="var(--grey-mid)" stroke-width="4" fill="none"/>
    <path d="M200 1066 C480 1056 700 1066 896 1090" stroke="var(--pink)" stroke-width="2" fill="none"/>
    <circle cx="160" cy="1029" r="92" fill="#ffffff"/>
    <circle cx="160" cy="1029" r="86" fill="none" stroke="var(--pink)" stroke-width="4"/>
  </svg>

  <div class="ceo-photo" role="img" aria-label="Portrait photo of the CEO"
       style="background:radial-gradient(circle at 50% 40%,#d9d6cf 0%,#a9a39a 60%,#8aa860 100%)"></div>

  <p class="ceo-name">Dana Whitfield, CEO</p>
  <p class="ceo-phone">
    <svg width="16" height="16" viewBox="0 0 24 24"><path d="M6.6 10.8a15 15 0 0 0 6.6 6.6l2.2-2.2a1 1 0 0 1 1-.25 11.4 11.4 0 0 0 3.6.57 1 1 0 0 1 1 1V20a1 1 0 0 1-1 1A17 17 0 0 1 3 4a1 1 0 0 1 1-1h3.5a1 1 0 0 1 1 1c0 1.25.2 2.45.57 3.6a1 1 0 0 1-.25 1z" fill="var(--grey-dark)"/></svg>
    (555)-0142738
  </p>

  <div class="footer-contact">
    <span><svg width="15" height="13" viewBox="0 0 24 20"><path d="M2 7l10 6 10-6v11H2z M2 7l10-6 10 6" fill="none" stroke="#fff" stroke-width="2"/></svg>P.O. Box 4821 Brookvale, GA 30999</span>
    <span><svg width="17" height="17" viewBox="0 0 24 24"><circle cx="12" cy="12" r="9.5" fill="none" stroke="#fff" stroke-width="2"/><path d="M2.5 12h19M12 2.5c3 3 3 16 0 19M12 2.5c-3 3-3 16 0 19" fill="none" stroke="#fff" stroke-width="1.6"/></svg>lumenhealthconsult@example.com</span>
  </div>
</article>
</body>
</html>
```